Business card design Needed for new logo / Construction business, home extensions and new builds

We need a business card design using our new logo files which i will attach to this project :)

We are a small construction business specialising in home extensions, new builds and property development. We are very ambitious and would appreciate professional and elegant designs for our new business card.

Very serious about using the services on MakerQuarry and recently acquired our new logo from here :)

Please get involved, i will feedback when i can as i am very busy but can respond daily, thanks

Target Market(s)

People that want to build onto their houses, new building developments or adding too their existing property

Industry/Entity Type

Construction

Contact Information for Business Card

Renwick Tolliver Construction, Lionel Ashby (Managing Director), Tel 07822254961, email - info@renwick-tolliver, www.renwick-tolliver.co.uk

Colors

Designer to choose colors to be used in the design.

Requirements
Must have
• I like a deep grey on the back please. A lot of you have provided black from and back, try mixing things up a little. The black looks cool 😎 Thanks

```html
<!DOCTYPE html>
<html lang="en">
<head>
<meta charset="utf-8">
<title>Renwick Tolliver Construction – Business Card</title>
<link rel="stylesheet" href="https://fonts.googleapis.com/css2?family=Open+Sans:wght@400;600;700&display=swap">
<style>
  :root {
    --stage: #232323;
    --card-back: #1f2023;
    --card-front: #24252a;
    --layer-mid: #1d1e22;
    --layer-low: #191a1d;
    --gold: #d9a23a;
    --gold-deep: #b07a1c;
    --silver: #d9dadc;
    --white: #f4f4f4;
    --ink: #1a1a1a;
  }
  * { box-sizing: border-box; margin: 0; padding: 0; }
  html, body {
    width: 1200px; height: 780px; overflow: hidden;
    background: var(--stage);
    font-family: "Open Sans", Arial, sans-serif;
  }
  .canvas {
    position: relative; width: 1200px; height: 780px;
    display: flex; justify-content: center; align-items: center; gap: 60px;
  }
  .card {
    position: relative; width: 340px; height: 580px;
    border-radius: 26px; overflow: hidden;
    box-shadow: 0 18px 40px rgba(0,0,0,.55);
  }

  /* Back */
  .card--back { background: var(--card-back); }
  .back-pattern {
    position: absolute; inset: 0;
    background: linear-gradient(135deg, #6b6c70 0%, #3a3b3f 22%, #242529 42%, #1c1d20 100%);
  }

  /* Front */
  .card--front { background: var(--card-front); color: var(--white); }
  .front-layers { position: absolute; inset: 0; }
  .brand {
    position: absolute; top: 70px; left: 0; right: 0;
    display: flex; flex-direction: column; align-items: center; gap: 14px;
  }
  .brand-dot {
    width: 52px; height: 52px; border-radius: 50%; background: var(--gold);
  }
  .brand-name {
    font-weight: 600; font-size: 17px; letter-spacing: 2px;
    text-transform: uppercase; color: var(--silver); text-align: center; line-height: 1.4;
  }
  .person {
    position: absolute; top: 238px; left: 0; right: 0; text-align: center;
  }
  .person-name { font-weight: 700; font-size: 30px; line-height: 1.1; }
  .person-name .first { color: var(--silver); }
  .person-name .last { color: var(--gold); }
  .person-role { font-weight: 600; font-size: 14px; margin-top: 4px; color: var(--white); }
  .contact-icons {
    display: flex; justify-content: center; gap: 8px; margin-top: 14px;
  }
  .icon-disc {
    width: 26px; height: 26px; border-radius: 50%;
    background: radial-gradient(circle at 35% 30%, #f3c867, var(--gold) 55%, var(--gold-deep));
    display: flex; align-items: center; justify-content: center;
  }
  .contact-list {
    list-style: none; margin-top: 12px; font-size: 13.5px; line-height: 1.45; color: var(--white);
  }
  .address {
    position: absolute; bottom: 46px; left: 0; right: 0; text-align: center;
    font-size: 14px; line-height: 1.45; color: var(--white);
  }
  .address .icon-disc { margin: 0 auto 10px; width: 28px; height: 28px; }
</style>
</head>
<body>
<main class="canvas">

  <section class="card card--back" aria-label="Card back">
    <div class="back-pattern" role="img" aria-label="Repeating monogram pattern with a soft silver sheen fading into deep grey"></div>
  </section>

  <section class="card card--front" aria-label="Card front">
    <svg class="front-layers" width="340" height="580" viewBox="0 0 340 580" aria-hidden="true">
      <defs>
        <filter id="layer-shadow" x="-20%" y="-20%" width="140%" height="140%">
          <feDropShadow dx="0" dy="6" stdDeviation="8" flood-color="#000" flood-opacity=".45"/>
        </filter>
      </defs>
      <rect width="340" height="580" fill="var(--layer-low)"/>
      <path d="M0 0 H340 V400 C300 470 220 505 130 505 C70 505 25 495 0 480 Z" fill="var(--layer-mid)" filter="url(#layer-shadow)"/>
      <path d="M0 0 H340 V330 C320 420 240 470 140 478 C80 482 30 470 0 455 Z" fill="var(--card-front)" filter="url(#layer-shadow)"/>
    </svg>

    <header class="brand">
      <span class="brand-dot" aria-hidden="true"></span>
      <p class="brand-name">Renwick Tolliver<br>Construction</p>
    </header>

    <div class="person">
      <h1 class="person-name"><span class="first">Lionel</span> <span class="last">Ashby</span></h1>
      <p class="person-role">Managing Director</p>
      <div class="contact-icons" aria-hidden="true">
        <span class="icon-disc">
          <svg width="14" height="14" viewBox="0 0 24 24"><path d="M6.6 10.8a15 15 0 0 0 6.6 6.6l2.2-2.2a1 1 0 0 1 1-.25 11.4 11.4 0 0 0 3.6.57 1 1 0 0 1 1 1V20a1 1 0 0 1-1 1A17 17 0 0 1 3 4a1 1 0 0 1 1-1h3.5a1 1 0 0 1 1 1c0 1.25.2 2.45.57 3.57a1 1 0 0 1-.25 1z" fill="var(--ink)"/></svg>
        </span>
        <span class="icon-disc">
          <svg width="14" height="14" viewBox="0 0 24 24"><rect x="3" y="6" width="18" height="12" rx="1.5" fill="none" stroke="var(--ink)" stroke-width="2"/><path d="M3 7l9 6 9-6" fill="none" stroke="var(--ink)" stroke-width="2"/></svg>
        </span>
        <span class="icon-disc">
          <svg width="14" height="14" viewBox="0 0 24 24"><circle cx="12" cy="12" r="9" fill="none" stroke="var(--ink)" stroke-width="2"/><ellipse cx="12" cy="12" rx="4" ry="9" fill="none" stroke="var(--ink)" stroke-width="1.6"/><path d="M3 12h18" stroke="var(--ink)" stroke-width="1.6"/></svg>
        </span>
      </div>
      <ul class="contact-list">
        <li>0782 225 4961</li>
        <li>info@renwick-tolliver.co.uk</li>
        <li>www.renwick-tolliver.co.uk</li>
      </ul>
    </div>

    <address class="address" style="font-style: normal;">
      <span class="icon-disc" aria-hidden="true">
        <svg width="14" height="14" viewBox="0 0 24 24"><path d="M12 2a7 7 0 0 0-7 7c0 5 7 13 7 13s7-8 7-13a7 7 0 0 0-7-7z" fill="var(--ink)"/><circle cx="12" cy="9" r="2.6" fill="var(--gold)"/></svg>
      </span>
      Kestrel Road, Ashgrove<br>
      Tideford, TD4 7QR
    </address>
  </section>

</main>
</body>
</html>
```